Business card for Luxury Portable Restroom Trailer company

We are a Luxury Portable Restroom Trailer Company Called FALCRIDGE HIRES. Based in Orange County California. We provide portable restroom trailers for events, such as, Weddings, Concerts, Charity events, Sporting events, Tournaments, Corporate events, ect. We rent and Sell the Luxury restrooms. Our colors are white, grey, and Orange. As you will see in the logo we uploaded.
There are 2 people in the company so the names and titles will change for the 3 people but card will remain the same. Here is the information for each Person: Dwight Penner CFO 555 318-0476
next Person: Leon Marchetti VP 555 318-0476
Next Person: Owen Marchetti CEO 555 318-0476
Information to include on the card: Luxury Restroom Trailers Rental and Sales. Weddings, Concerts, Charity, Sporting and Corp. Events.

```html
<!DOCTYPE html>
<html lang="en">
<head>
<meta charset="utf-8">
<title>Falcridge Hires – Business Card</title>
<link rel="stylesheet" href="https://fonts.googleapis.com/css2?family=Montserrat:wght@400;500;700;800;900&display=swap">
<style>
  :root {
    --orange: #f26c23;
    --grey: #58595b;
    --ink: #1e1e1e;
    --white: #ffffff;
    --backdrop: #e6e6e6;
  }
  * { box-sizing: border-box; margin: 0; padding: 0; }
  html, body {
    width: 1200px;
    height: 856px;
    overflow: hidden;
    background: var(--backdrop);
    font-family: "Montserrat", Arial, sans-serif;
  }
  .canvas {
    width: 1200px;
    height: 856px;
    display: flex;
    align-items: center;
    justify-content: center;
    gap: 40px;
  }
  .card {
    position: relative;
    width: 560px;
    height: 320px;
    overflow: hidden;
    box-shadow: 0 10px 28px rgba(0,0,0,0.22);
  }

  /* Front */
  .card--front { background: var(--white); }
  .card__wave {
    position: absolute;
    inset: 0;
    width: 100%;
    height: 100%;
  }
  .wordmark {
    position: absolute;
    top: 30px;
    right: 30px;
    text-align: right;
    font-weight: 900;
    color: var(--grey);
    line-height: 1.05;
    letter-spacing: 1px;
  }
  .wordmark__line { display: block; font-size: 32px; }
  .wordmark__line--small { font-size: 20px; letter-spacing: 5px; color: var(--grey); }

  .team {
    position: absolute;
    left: 32px;
    top: 96px;
    display: flex;
    flex-direction: column;
    gap: 8px;
  }
  .person__name {
    color: var(--orange);
    font-weight: 800;
    font-size: 15px;
    letter-spacing: 0.5px;
    text-transform: uppercase;
    line-height: 1.15;
  }
  .person__title {
    color: var(--ink);
    font-size: 12px;
    font-weight: 500;
    line-height: 1.3;
  }
  .person__phone {
    display: flex;
    align-items: center;
    gap: 6px;
    color: var(--ink);
    font-size: 12px;
    font-weight: 500;
    line-height: 1.3;
  }
  .person__phone svg { width: 12px; height: 12px; fill: var(--orange); }

  /* Back */
  .card--back {
    background: var(--orange);
    color: var(--white);
    display: flex;
    flex-direction: column;
    align-items: center;
    justify-content: center;
    text-align: center;
  }
  .brand {
    font-weight: 900;
    line-height: 1;
    letter-spacing: 2px;
  }
  .brand__line { display: block; font-size: 56px; }
  .brand__line--small { font-size: 34px; letter-spacing: 10px; margin-top: 6px; }
  .services {
    margin-top: 34px;
    font-size: 14px;
    font-weight: 500;
    line-height: 1.7;
  }
  .services__item::before {
    content: "";
    display: inline-block;
    width: 7px;
    height: 7px;
    margin: 0 6px 2px 10px;
    border-radius: 50%;
    background: var(--white);
  }
</style>
</head>
<body>
<main class="canvas">

  <section class="card card--front" aria-label="Business card front">
    <svg class="card__wave" viewBox="0 0 560 320" preserveAspectRatio="none" aria-hidden="true">
      <path d="M0 288 C180 288 250 250 320 190 C390 130 450 118 560 112 L560 320 L0 320 Z" fill="var(--grey)"/>
      <path d="M0 300 C190 300 262 262 332 202 C400 145 460 133 560 128 L560 320 L0 320 Z" fill="var(--orange)"/>
    </svg>

    <div class="wordmark">
      <span class="wordmark__line">FALCRIDGE</span>
      <span class="wordmark__line wordmark__line--small">HIRES</span>
    </div>

    <div class="team">
      <div class="person">
        <p class="person__name">Dwight Penner</p>
        <p class="person__title">CFO</p>
        <p class="person__phone">
          <svg viewBox="0 0 24 24"><path d="M6.6 10.8a15.1 15.1 0 0 0 6.6 6.6l2.2-2.2a1 1 0 0 1 1-.25 11.4 11.4 0 0 0 3.6.57 1 1 0 0 1 1 1V20a1 1 0 0 1-1 1A17 17 0 0 1 3 4a1 1 0 0 1 1-1h3.5a1 1 0 0 1 1 1 11.4 11.4 0 0 0 .57 3.6 1 1 0 0 1-.25 1z"/></svg>
          555 318-0476
        </p>
      </div>
      <div class="person">
        <p class="person__name">Leon Marchetti</p>
        <p class="person__title">VP</p>
        <p class="person__phone">
          <svg viewBox="0 0 24 24"><path d="M6.6 10.8a15.1 15.1 0 0 0 6.6 6.6l2.2-2.2a1 1 0 0 1 1-.25 11.4 11.4 0 0 0 3.6.57 1 1 0 0 1 1 1V20a1 1 0 0 1-1 1A17 17 0 0 1 3 4a1 1 0 0 1 1-1h3.5a1 1 0 0 1 1 1 11.4 11.4 0 0 0 .57 3.6 1 1 0 0 1-.25 1z"/></svg>
          555 318-0476
        </p>
      </div>
      <div class="person">
        <p class="person__name">Owen Marchetti</p>
        <p class="person__title">CEO</p>
        <p class="person__phone">
          <svg viewBox="0 0 24 24"><path d="M6.6 10.8a15.1 15.1 0 0 0 6.6 6.6l2.2-2.2a1 1 0 0 1 1-.25 11.4 11.4 0 0 0 3.6.57 1 1 0 0 1 1 1V20a1 1 0 0 1-1 1A17 17 0 0 1 3 4a1 1 0 0 1 1-1h3.5a1 1 0 0 1 1 1 11.4 11.4 0 0 0 .57 3.6 1 1 0 0 1-.25 1z"/></svg>
          555 318-0476
        </p>
      </div>
    </div>
  </section>

  <section class="card card--back" aria-label="Business card back">
    <h1 class="brand">
      <span class="brand__line">FALCRIDGE</span>
      <span class="brand__line brand__line--small">HIRES</span>
    </h1>
    <div class="services">
      <p><span class="services__item">Luxury Restroom Trailers Rental and Sales</span></p>
      <p>
        <span class="services__item">Weddings</span>
        <span class="services__item">Concerts</span>
        <span class="services__item">Charity</span>
        <span class="services__item">Sporting and Corp</span>
        <span class="services__item">Events</span>
      </p>
    </div>
  </section>

</main>
</body>
</html>
```